Velmora Systems Website

Website design for our company: Velmora Systems.
The website should look fresh and IT focused. Please have a look at http://www.velmorasystems.example.au/ for our current design. We want something fresh and new, professional looking, in WordPress so we can easily make changes.

It Company

```html
<!DOCTYPE html>
<html lang="en">
<head>
<meta charset="utf-8">
<title>Velmora Systems</title>
<link rel="stylesheet" href="https://fonts.googleapis.com/css2?family=Open+Sans:wght@300;400;600;700&display=swap">
<style>
:root{
  --green:#0fad4f;
  --green-light:#3cc46d;
  --green-dark:#0a9642;
  --blue:#0a63b8;
  --blue-dark:#0b4f93;
  --ink:#3d3f44;
  --text:#4a4a4a;
  --muted:#8a8c90;
  --paper:#f4f4f4;
  --panel:#e9e9e9;
  --footer:#45474c;
  --footer-text:#c5c6c8;
  --quote:#909398;
}
*{box-sizing:border-box;margin:0;padding:0}
html,body{width:1024px;height:1200px;overflow:hidden}
body{font-family:"Open Sans",Arial,sans-serif;background:var(--paper);color:var(--text);position:relative}
.abs{position:absolute}
.topline{left:0;top:0;width:1024px;height:3px;background:var(--blue)}
.header{left:0;top:0;width:1024px;height:78px;background:#f6f6f6}
.brand{left:137px;top:8px;width:129px;height:64px;border:2px solid var(--green);background:#fff;border-radius:3px;display:flex;align-items:center;justify-content:center;gap:5px}
.brand .dot{flex:none;width:8px;height:8px;background:var(--green)}
.brand span{font-size:12px;font-weight:700;color:var(--green);white-space:nowrap}
.remote{left:632px;top:0;width:264px;height:42px;background:var(--blue);border-radius:0 0 5px 5px}
.remote .label{left:15px;top:7px;color:#fff;font-size:10.5px;font-weight:700;line-height:13px}
.remote .field{left:80px;top:8px;width:176px;height:26px;background:#3e4146;border-radius:3px}
.remote .field span{left:8px;top:8px;font-size:7.5px;color:#cfd0d2;white-space:nowrap}
.remote .btn{right:2px;top:2px;width:52px;height:22px;background:#55585d;border-radius:3px;font-size:7.5px;color:#ddd;text-align:center;line-height:22px}
.nav{left:0;top:78px;width:1024px;height:38px;background:linear-gradient(var(--green-light),var(--green));border-top:1px solid #0c9c46}
.nav a{position:absolute;top:12px;color:#fff;font-size:11px;font-weight:700;text-decoration:none}
.search{left:712px;top:4px;width:176px;height:28px;background:#f2f2f2;border-radius:3px}
.search span{left:8px;top:8px;font-size:10px;color:#999}
.hero{left:0;top:116px;width:1024px;height:322px;background:linear-gradient(90deg,#d9dde2,#eef1f3 40%,#c9ced6 60%,#e6e9ec)}
.arrow{width:38px;height:38px;border-radius:50%;border:3px solid #e6e6e6;display:flex;align-items:center;justify-content:center}
.band{left:0;top:438px;width:1024px;height:84px;background:linear-gradient(90deg,var(--green) 20%,var(--green-light) 45%,var(--green))}
.band h1{left:138px;top:17px;font-size:24px;font-weight:300;color:#fff;white-space:nowrap}
.band p{left:141px;top:46px;font-size:14.4px;color:#fff}
.intro{left:0;top:522px;width:1024px;height:204px;background:var(--panel)}
h2.sec{position:absolute;font-size:19px;font-weight:400;color:var(--ink)}
.avatar{border-radius:50%;background:linear-gradient(#cfcfcf,#8c8c8c);border:3px solid #fafafa;box-shadow:0 0 0 1px #ccc}
.intro .copy{left:218px;top:63px;width:255px;font-size:10.4px;line-height:16px;color:var(--text)}
.readmore{left:218px;top:147px;width:83px;height:27px;background:#f5f5f5;border:1px solid #ccc;border-radius:3px;font-size:7.5px;text-align:center;line-height:25px;color:#555}
.person{left:521px;top:125px;font-size:7.5px;line-height:10px;color:#555;white-space:nowrap}
.person b{font-size:8.5px;color:#333}
.quote{left:612px;top:67px;width:276px;height:104px;background:var(--quote);border-radius:3px;box-shadow:0 4px 0 #c4c5c7;padding:24px 25px;font-size:10.4px;line-height:16px;color:#fff}
.quote:before{content:"";position:absolute;left:-18px;top:16px;border:9px solid transparent;border-right-color:var(--quote);border-top-color:var(--quote)}
.services{left:0;top:726px;width:1024px;height:244px;background:#f4f4f4}
.rule{left:136px;top:78px;width:752px;height:2px;background:#ddd}
.rule:after{content:"";position:absolute;left:369px;top:2px;border:5px solid transparent;border-top-color:#ddd}
.svc{position:absolute;display:flex;align-items:center;gap:9px;font-size:11.2px;font-weight:700;color:var(--ink);line-height:16px}
.svc i{flex:none;width:32px;height:32px;border-radius:50%;background:var(--ink);display:flex;align-items:center;justify-content:center}
.svc.active{color:#1f6fb8}
.svc.active i{background:#3b8fd6;box-shadow:0 0 0 2px #cfe3f5}
.footer{left:0;top:970px;width:1024px;height:216px;background:var(--footer);color:var(--footer-text)}
.footer h3{position:absolute;font-size:11.2px;font-weight:700;color:#d3d4d6}
.fbrand{left:138px;top:34px;width:149px;height:62px;border:2px solid var(--green);background:#fff;border-radius:3px;display:flex;align-items:center;justify-content:center;gap:6px}
.fbrand .dot{flex:none;width:10px;height:10px;background:var(--green)}
.fbrand span{font-size:14px;font-weight:700;color:var(--green);white-space:nowrap}
.copyright{left:137px;top:172px;font-size:9px;color:#7d7f83}
.flist{left:365px;top:64px;list-style:none;font-size:10px;line-height:16px}
.flist li:before{content:"";display:inline-block;border:3px solid transparent;border-left-color:#bbb;margin-right:4px}
.contact{left:521px;top:64px;font-size:10px;line-height:16px}
.fsupport{left:713px;top:66px;font-size:9px}
.finput{left:713px;top:90px;width:175px;height:26px;background:#3a3c40;border-radius:3px}
.finput .btn{right:2px;top:2px;width:52px;height:22px;background:#55585d;border-radius:3px;font-size:7.5px;color:#ddd;text-align:center;line-height:22px;position:absolute}
.socials{left:713px;top:160px;display:flex;gap:14px}
.socials span{width:13px;height:13px;border-radius:50%;background:#6b6d72}
.bottom{left:0;top:1186px;width:1024px;height:14px;background:var(--green)}
</style>
</head>
<body>
<div class="abs header"></div>
<div class="abs topline"></div>
<div class="abs brand"><div class="dot"></div><span>Velmora Systems</span></div>
<div class="abs remote">
  <div class="abs label">REMOTE<br>SUPPORT</div>
  <div class="abs field"><span class="abs">ENTER -6 DIGIT CODE</span><div class="abs btn">CONNECT</div></div>
</div>

<nav class="abs nav">
  <a style="left:152px">HOME</a><a style="left:244px">SERVICES</a><a style="left:356px">PORTFOLIO</a><a style="left:478px">ABOUT</a><a style="left:581px">CONTACTS</a>
  <div class="abs search"><span class="abs">Search the site</span>
    <svg class="abs" style="right:8px;top:7px" width="14" height="14" viewBox="0 0 14 14"><circle cx="8.5" cy="5.5" r="4" fill="none" stroke="#666" stroke-width="1.3"/><line x1="5.5" y1="8.5" x2="1.5" y2="12.5" stroke="#666" stroke-width="1.5"/></svg>
  </div>
</nav>

<div class="abs hero" role="img" aria-label="Photo of business professionals in a meeting around a table"></div>
<div class="abs arrow" style="left:89px;top:259px;background:var(--blue-dark)"><svg width="8" height="8" viewBox="0 0 8 8"><path d="M5 1L2 4l3 3" stroke="#fff" fill="none" stroke-width="1.4"/></svg></div>
<div class="abs arrow" style="left:894px;top:259px;background:#5a5d62"><svg width="8" height="8" viewBox="0 0 8 8"><path d="M3 1l3 3-3 3" stroke="#fff" fill="none" stroke-width="1.4"/></svg></div>

<div class="abs band">
  <h1 class="abs">Velmora Systems is an Adelaide based company with a single objective</h1>
  <p class="abs">- to excel in the support and service of all computer and IT needs.</p>
</div>

<section class="abs intro">
  <h2 class="sec" style="left:138px;top:25px">WELCOME TO OUR SITE!</h2>
  <div class="abs avatar" role="img" aria-label="Portrait photo of a team member" style="left:138px;top:65px;width:68px;height:68px"></div>
  <p class="abs copy">Because we know you don’t want to be limited on a portrait or scape format we made Showcase. compatible in both portrait AND landscape! Yes, we care about you.</p>
  <div class="abs readmore">READ MORE</div>

  <h2 class="sec" style="left:521px;top:25px">WHAT PEOPLE SAY</h2>
  <div class="abs avatar" role="img" aria-label="Portrait photo of a client" style="left:522px;top:65px;width:52px;height:52px"></div>
  <div class="abs person"><b>NADIA VOSS</b><br>CEO, NORVA GROUP</div>
  <div class="abs quote">Because we know you don’t want to be limited on a portrait or scape format we made Showcase. compatible in both portrait AND landscape!</div>
</section>

<section class="abs services">
  <h2 class="sec" style="left:0;width:1000px;text-align:center;top:36px">OUR SERVICES</h2>
  <div class="abs rule"></div>
  <div class="svc active" style="left:137px;top:105px"><i><svg width="14" height="14" viewBox="0 0 14 14"><circle cx="7" cy="7" r="6" fill="#fff"/><rect x="4" y="5.5" width="6" height="1" fill="#3b8fd6"/><rect x="4" y="7.5" width="6" height="1" fill="#3b8fd6"/></svg></i>ON-SITE SERVICE</div>
  <div class="svc" style="left:329px;top:105px"><i><svg width="14" height="14" viewBox="0 0 14 14"><rect x="3" y="3" width="8" height="8" fill="none" stroke="#fff" stroke-width="1.4"/></svg></i>MEDICAL IT SERVICE</div>
  <div class="svc" style="left:522px;top:105px"><i><svg width="14" height="14" viewBox="0 0 14 14"><circle cx="7" cy="7" r="5.5" fill="none" stroke="#fff" stroke-width="1.4"/><line x1="1.5" y1="7" x2="12.5" y2="7" stroke="#fff"/></svg></i>REMOTE DESKTOP</div>
  <div class="svc" style="left:714px;top:105px"><i><svg width="14" height="14" viewBox="0 0 14 14"><path d="M5 2h4v3l3 7H2l3-7z" fill="#fff"/></svg></i>PHARMACY IT SERVICE</div>
  <div class="svc" style="left:137px;top:164px"><i><svg width="14" height="14" viewBox="0 0 14 14"><rect x="3" y="1.5" width="8" height="11" fill="none" stroke="#fff" stroke-width="1.3"/><circle cx="7" cy="8" r="1.6" fill="#fff"/></svg></i>HARDWARE/ SOFTWARE<br>SUPPLY</div>
  <div class="svc" style="left:329px;top:164px"><i><svg width="14" height="14" viewBox="0 0 14 14"><path d="M12 2L5 9l-1 3 3-1 7-7z" fill="#fff"/></svg></i>WEBSITE DESIGN</div>
  <div class="svc" style="left:522px;top:164px"><i><svg width="14" height="14" viewBox="0 0 14 14"><path d="M7 1l6 6-6 6-6-6z" fill="none" stroke="#fff" stroke-width="1.6"/></svg></i>DISASTER RECOVERY</div>
  <div class="svc" style="left:714px;top:164px"><i><svg width="14" height="14" viewBox="0 0 14 14"><g stroke="#fff" stroke-width="1.4"><line x1="3" y1="2" x2="3" y2="12"/><line x1="6" y1="2" x2="6" y2="12"/><line x1="9" y1="2" x2="9" y2="12"/><line x1="12" y1="2" x2="12" y2="12"/></g></svg></i>CONSUMABLES</div>
</section>

<footer class="abs footer">
  <div class="abs fbrand"><div class="dot"></div><span>Velmora Systems</span></div>
  <div class="abs copyright">© 2014 Velmora Systems. All Rights Reserved</div>
  <h3 style="left:365px;top:36px">NAVIGATION</h3>
  <ul class="abs flist"><li>HOME</li><li>CLIENTS</li><li>SERVICES</li><li>SUPPORTS</li><li>TESTIMONIALS</li><li>CONTACT US</li><li>ABOUT US</li></ul>
  <h3 style="left:521px;top:36px">CONTACTS</h3>
  <div class="abs contact">Kestrel Holdings<br>PO Box 40562<br>Harrow Lane, Ashbury<br>Victoria 8890 Australia<br><br>Phone: (08) 5550 1934<br>support@velmorasystems.example.au</div>
  <h3 style="left:713px;top:36px">REMOTE SUPPORT</h3>
  <div class="abs fsupport">Enter you 6-digit code</div>
  <div class="abs finput"><div class="btn">CONNECT</div></div>
  <h3 style="left:713px;top:136px">GET SOCIAL</h3>
  <div class="abs socials"><span></span><span></span><span></span><span></span><span></span></div>
</footer>
<div class="abs bottom"></div>
</body>
</html>
```